Naturopath Practitioner Card Design

I am a naturopath needing a design for a business card mainly to show that I am a naturopath and have some contact details to give to prospective clients. I am open minded about the design and what is on the second side of the card whether it just be some artwork or space for details, appointment times etc. Naturopathy is the practice of natural medicine that uses a holistic approach and incorporates herbal and nutritional medicine.

Industry/Entity Type

Business

Contact Information for Business Card

Tom Rudd NaturopathBHSc (Naturopathy) Member WHPG 0487 925 316 tom.rudd@mailexample.com www.tomruddnaturopathy.example.au

Requirements
Nice to have
• Would prefer some kind of original pattern/art work/logo rather than an image, not fussed if its very simple/basic
• I am open to any colour but think I would prefer a more earthy sandy clay etc type style than the greens that are commonly associated with naturopathy.
Should not have
• Don't really want to have generic stock images on it

```html
<!DOCTYPE html>
<html lang="en">
<head>
<meta charset="utf-8">
<title>Tom Rudd Naturopath – Business Card</title>
<link href="https://fonts.googleapis.com/css2?family=Open+Sans:wght@400;600;700&display=swap" rel="stylesheet">
<style>
  :root {
    --stage-top: #2b2b2b;
    --stage-bottom: #080808;
    --card-front: #f3f3f3;
    --card-back: #ffffff;
    --brand-green: #1e9e1e;
    --leaf-dark: #2f7d16;
    --leaf-light: #8fd13a;
    --ink: #111111;
  }
  * { margin: 0; padding: 0; box-sizing: border-box; }
  html, body { width: 1200px; height: 900px; overflow: hidden; }
  body {
    font-family: "Open Sans", Arial, sans-serif;
    background: linear-gradient(180deg, var(--stage-top) 0%, #1a1a1a 45%, var(--stage-bottom) 100%);
    position: relative;
  }
  .card {
    position: absolute;
    top: 184px;
    height: 491px;
    border-radius: 12px;
    overflow: hidden;
  }
  .card--front { left: 299px; width: 301px; background: var(--card-front); }
  .card--back  { left: 645px; width: 305px; background: var(--card-back); }

  .foliage {
    position: absolute;
    background: linear-gradient(160deg, var(--leaf-light), var(--leaf-dark));
  }
  .foliage--left  { left: 0; top: 0; width: 38px; height: 100%; border-radius: 0 40px 40px 0 / 0 200px 200px 0; }
  .foliage--right { right: 0; top: 0; width: 42px; height: 100%; border-radius: 40px 0 0 40px / 200px 0 0 200px; }
  .foliage--corner-top { left: 0; top: 0; width: 135px; height: 135px; border-radius: 0 0 100% 0; }
  .foliage--corner-bottom { right: 0; bottom: 0; width: 130px; height: 135px; border-radius: 100% 0 0 0; }

  .front-name {
    position: absolute; left: 0; right: 0; top: 156px;
    text-align: center; color: var(--brand-green);
    font-weight: 700; font-size: 26px; letter-spacing: 0.5px;
  }
  .front-role {
    position: absolute; left: 0; right: 0; top: 184px;
    text-align: center; color: var(--ink); font-size: 17px;
  }
  .front-credentials {
    position: absolute; left: 0; right: 0; top: 206px;
    text-align: center; color: var(--ink); font-size: 12.5px;
  }
  .contact {
    position: absolute; left: 0; right: 0;
    display: flex; justify-content: center; align-items: center; gap: 6px;
    color: var(--ink); font-size: 14px;
  }
  .contact--phone { top: 298px; }
  .contact--email { top: 320px; }
  .contact svg { flex: none; }

  .back-title {
    position: absolute; left: 0; right: 0; top: 134px;
    text-align: center; color: var(--brand-green);
    font-weight: 600; font-size: 20px;
  }
  .field {
    position: absolute; left: 14px; right: 10px;
    color: var(--ink); font-size: 14px; font-weight: 600; white-space: nowrap;
  }
  .field .dots { font-weight: 400; letter-spacing: -0.5px; }
  .field--name { top: 216px; }
  .field--datetime { top: 272px; }
  .notice {
    position: absolute; left: 0; right: 0; top: 333px;
    text-align: center; color: var(--brand-green);
    font-weight: 700; font-size: 15px; line-height: 21px;
    font-variant: small-caps;
  }
</style>
</head>
<body>
  <section class="card card--front" aria-label="Card front">
    <div class="foliage foliage--left" role="img" aria-label="Green leaf foliage border"></div>
    <div class="foliage foliage--right" role="img" aria-label="Green leaf foliage border"></div>
    <h1 class="front-name">TOM RUDD</h1>
    <p class="front-role">Naturopath</p>
    <p class="front-credentials">BHSc (Naturopathy) Member WHPG</p>
    <p class="contact contact--phone">
      <svg width="13" height="13" viewBox="0 0 24 24" aria-hidden="true"><path fill="var(--brand-green)" d="M6.6 10.8a15.1 15.1 0 0 0 6.6 6.6l2.2-2.2c.3-.3.7-.4 1-.2 1.1.4 2.3.6 3.6.6.6 0 1 .4 1 1V20c0 .6-.4 1-1 1A17 17 0 0 1 3 4c0-.6.4-1 1-1h3.5c.6 0 1 .4 1 1 0 1.3.2 2.5.6 3.6.1.3 0 .7-.2 1z"/></svg>
      <span>0487 925 316</span>
    </p>
    <p class="contact contact--email">
      <svg width="15" height="11" viewBox="0 0 15 11" aria-hidden="true"><rect width="15" height="11" fill="var(--brand-green)"/><path d="M0.5 0.8 7.5 6 14.5 0.8" fill="none" stroke="#fff" stroke-width="1.2"/></svg>
      <span>tom.rudd@mailexample.com</span>
    </p>
  </section>

  <section class="card card--back" aria-label="Card back">
    <div class="foliage foliage--corner-top" role="img" aria-label="Green leaf cluster in corner"></div>
    <div class="foliage foliage--corner-bottom" role="img" aria-label="Green leaf cluster in corner"></div>
    <h2 class="back-title">Your Next Appointment on</h2>
    <p class="field field--name">Name : <span class="dots">........................................................</span></p>
    <p class="field field--datetime">Date : <span class="dots">..................</span> Time : <span class="dots">..................</span> <span style="font-weight:400">AM / PM</span></p>
    <p class="notice">If unable to keep appointment,<br>kindly give 24hrs notice.</p>
  </section>
</body>
</html>
```